SEASONING LABEL RE-DESIGN

We are looking for someone to redesign our clients seasoning labels to look more professional and store ready

Please see attached details..

Target Market(s)

People who cook

Industry/Entity Type

Food Industry

Font styles to use
Sans Serif

Requirements
Must have
• Bold but FUN !

```html
<!DOCTYPE html>
<html lang="en">
<head>
<meta charset="utf-8">
<title>Ridgeline Seasoning – Margarita Chicken Label</title>
<link href="https://fonts.googleapis.com/css2?family=Alfa+Slab+One&family=Oswald:wght@500;600&family=Roboto+Condensed:wght@400&display=swap" rel="stylesheet">
<style>
  :root {
    --page: #ffffff;
    --label-red: #e23b22;
    --label-red-deep: #c92d17;
    --charcoal: #1d1d1f;
    --charcoal-light: #3a3b3f;
    --ink-white: #ffffff;
    --soft-white: #e9e9e9;
    --texas-green: #6db33f;
    --gold: #c99a3b;
  }
  * { box-sizing: border-box; margin: 0; padding: 0; }
  html, body { width: 1200px; height: 1200px; overflow: hidden; background: var(--page); }
  .canvas { position: relative; width: 1200px; height: 1200px; }

  .label {
    position: absolute; left: 50px; top: 300px; width: 1100px; height: 600px;
    background: var(--charcoal); overflow: hidden;
  }
  .band { position: absolute; left: 0; width: 100%; height: 44px; background: var(--label-red); }
  .band--top { top: 0; }
  .band--bottom { bottom: 0; }

  .texture {
    position: absolute; left: 0; top: 44px; width: 100%; height: 512px;
    background: radial-gradient(ellipse at 40% 40%, var(--charcoal-light), var(--charcoal) 70%);
  }

  /* Nutrition side panel */
  .nutrition {
    position: absolute; left: 30px; top: 80px; width: 200px;
    font-family: "Roboto Condensed", sans-serif; color: var(--soft-white);
  }
  .nutrition table { width: 100%; border-collapse: collapse; font-size: 12px; }
  .nutrition td { border: 1px solid var(--soft-white); padding: 4px 6px; }
  .nutrition td.value { text-align: right; }
  .nutrition .title { font-size: 14px; font-weight: 400; }
  .ingredients { margin-top: 16px; font-size: 12.5px; line-height: 1.45; text-align: justify; }

  /* Brand name */
  .brand {
    position: absolute; left: 290px; top: 90px; width: 520px; text-align: center;
    font-family: "Alfa Slab One", serif; color: var(--soft-white);
  }
  .brand__mark {
    display: block; width: 22px; height: 22px; margin: 0 auto 14px;
    border-radius: 50%; background: var(--gold);
  }
  .brand__name { font-size: 58px; line-height: 1; letter-spacing: 1px; }
  .brand__sub { font-size: 30px; line-height: 1.2; letter-spacing: 4px; margin-top: 6px; }

  /* Flavour panel */
  .flavour {
    position: absolute; left: 300px; top: 300px; width: 500px; height: 230px;
    background: var(--label-red);
  }
  .flavour__frame {
    position: absolute; inset: 14px; border: 2px solid var(--soft-white);
  }
  .flavour__name {
    position: absolute; left: 34px; top: 36px; font-family: "Alfa Slab One", serif;
    color: var(--ink-white); line-height: 1;
  }
  .flavour__name .line1 { font-size: 27px; letter-spacing: 1px; }
  .flavour__name .line2 { font-size: 40px; margin-top: 6px; display: block; }
  .crafted {
    position: absolute; left: 36px; top: 124px; width: 196px; height: 36px;
    background: var(--texas-green); color: var(--ink-white);
    font-family: "Oswald", sans-serif; font-weight: 600; font-size: 22px;
    line-height: 36px; text-align: center;
  }
  .divider-v { position: absolute; left: 262px; top: 40px; width: 2px; height: 116px; background: var(--soft-white); }
  .divider-h { position: absolute; left: 34px; right: 34px; top: 172px; height: 2px; background: var(--soft-white); }
  .claim-badge {
    position: absolute; left: 320px; top: 48px; width: 96px; height: 96px;
    border: 3px solid var(--soft-white); border-radius: 50%;
  }
  .footer-line {
    position: absolute; left: 34px; top: 182px; font-family: "Oswald", sans-serif;
    font-weight: 500; font-size: 17px; color: var(--ink-white); letter-spacing: 0.5px;
    display: flex; align-items: center; gap: 12px;
  }
  .footer-line .sep { width: 2px; height: 24px; background: var(--soft-white); }
  .signature { width: 110px; height: 28px; background: linear-gradient(90deg, var(--label-red-deep), var(--label-red)); }

  /* Story panel */
  .story {
    position: absolute; left: 880px; top: 82px; width: 196px;
    font-family: "Alfa Slab One", serif; color: var(--ink-white);
    font-size: 21px; line-height: 1.28; text-transform: uppercase;
  }
  .story .big { font-size: 30px; }
  .story .url {
    display: block; margin-top: 24px; font-family: "Oswald", sans-serif;
    font-weight: 500; font-size: 16px; letter-spacing: 0.5px;
  }
</style>
</head>
<body>
<main class="canvas">
  <section class="label" aria-label="Seasoning jar label">
    <div class="band band--top"></div>
    <div class="texture" role="img" aria-label="Dark grunge texture background"></div>
    <div class="band band--bottom"></div>

    <aside class="nutrition">
      <table>
        <tr><td colspan="2" class="title">Nutrition Facts</td></tr>
        <tr><td>Serving Size</td><td class="value">1g</td></tr>
        <tr><td>Amount / Grams</td><td class="value">%Daily Value</td></tr>
        <tr><td>Calories 0</td><td class="value">0.0%</td></tr>
        <tr><td>Total Fat 0</td><td class="value">0.0%</td></tr>
        <tr><td>Sodium 191</td><td class="value">8.0%</td></tr>
        <tr><td>Carbs &lt;1g</td><td class="value">0.0%</td></tr>
        <tr><td>Protein 0</td><td class="value">0.0%</td></tr>
      </table>
      <p class="ingredients">Ingredients: salt, citric acid, onion, monosodium glutamate, garlic, celery, spice including turmeric, grill flavor, parsley and not more than 2% silicon dioxide to prevent caking.</p>
    </aside>

    <header class="brand">
      <span class="brand__mark"></span>
      <div class="brand__name">RIDGELINE</div>
      <div class="brand__sub">SEASONING</div>
    </header>

    <div class="flavour">
      <div class="flavour__frame"></div>
      <h1 class="flavour__name"><span class="line1">MARGARITA</span><span class="line2">CHICKEN</span></h1>
      <div class="crafted">CRAFTED IN TEXAS</div>
      <div class="divider-v"></div>
      <div class="claim-badge"></div>
      <div class="divider-h"></div>
      <div class="footer-line">
        <span>NET WT 8OZ</span><span class="sep"></span><span>MADE WITH LOVE BY</span>
        <span class="signature" role="img" aria-label="Handwritten signature of Sam &amp; Dana Morrow"></span>
      </div>
    </div>

    <aside class="story">
      Ridgeline seasoning is a low sodium seasoning company providing <span class="big">unique</span> seasoning blends sure to "tickle the taste buds" of any palate without the high sodium intake!
      <span class="url">RIDGELINEFLAVOR.COM</span>
    </aside>
  </section>
</main>
</body>
</html>
```